Brivora Distance Learning Website

Brivora provide e-learning and mixed learning solutions for individuals, colleges, organisations and B2B.
We need a modern, light and flat website design for Brivora. We want to to see the designer incorporate user experience(UX) design elements into the AI or PSD mockups. We would like to see designs that use pastel colors that compliment yellow and black of our logo.
We want our E-learning experience to accelerate learning and for the interface to be user friendly and intuitive. We want the designs to focus on quick access to course information, course reviews, learning progress and study advice. Quick and intuitive access to all content for our clients is one of our top priorities.
We would like designs for the following project 3 pages:
1. Learner homepage dashboard (see attached screenshot).
On this page the Learners need to:
- Login
- Have quick access to Packages and Courses.
- See other recommended courses (Below Packages and Courses)
- Possibly a left hand side column/menu with thumbnail icons (See lumeqa learner dashboard screenshot)
2. Homepage
See current sample
http://www.brivora-learn.example
We would like the designer to focus on creating a customized banner to enhance the home page.
3. Primary Landing/Marketing page
This page is geared towards customer acquisition with the focal point being the top banner (video or HD image).
And Course Preview content below.
See reference
http://brivora-learn.example/subscriptionPlans/marketing/MTc%3D/Mjc4Nw%3D%3D/Speaking%20Nepali%20%2B%20Nepali%20Snacks%20Bundle%20by%20Lorne%20Pike%20Vell
Other site we like:
- https://www.skillorva.example (We like the home page and top bar on courses page)
- http://www.tutorcrest.example
- http://pixelgrovelab.example (think this site looks great, love the lower graphics on the homepage)
Updates
Hello,
Thank you for taking the time to contribute to this web design competition. We would just like to point out a few things:
1. Please try to make the color palette similar to the colors used in the screenshot that we just uploaded ('possible color palette).
2. Please make the designs specific to each page: THE LEARNER HOMEPAGE, HOME PAGE, and the MARKETING LANDING PAGE.
We are very happy with the high quality of designs so far,
Cheers,
Ned Ru
VK-Studio
Also,
Please avoid using dark/bold elements in the designs. The ONLY elements that we want to be dark are the logo and the footer.
Any questions please ask,
Cheers,
Ned Ru
Vk-Studio
Hello,
Based on the round of feedback we just gave it would be great if you could complete further design changes by tomorrow, as we are pushed for time.
Thank you,
Ned Ru
VK-Studio

```html
<!DOCTYPE html>
<html lang="en">
<head>
<meta charset="utf-8">
<title>Brivora – Your Learning Journey Starts Here</title>
<link rel="stylesheet" href="https://fonts.googleapis.com/css2?family=Roboto:wght@300;400;500;700&family=Ubuntu:wght@500;700&display=swap">
<style>
:root{
  --yellow:#f6b300;
  --yellow-2:#f7bd2c;
  --yellow-3:#f9cb55;
  --yellow-4:#fbd98a;
  --orange:#f39c12;
  --orange-dark:#e08600;
  --ink:#222;
  --text:#555;
  --muted:#888;
  --line:#d9d9d9;
  --hero-top:#8e8e8e;
  --hero-bottom:#6c6c6c;
  --footer:#6b6b6b;
  --link-blue:#2f9fd8;
  --icon:#8f846f;
}
*{box-sizing:border-box;margin:0;padding:0}
html,body{width:1200px;height:3251px;overflow:hidden}
body{position:relative;background:#fff;font-family:"Roboto",Arial,sans-serif;color:var(--text)}
.abs{position:absolute}

/* header */
.site-header{position:absolute;left:0;top:0;width:1200px;height:100px;background:#fff;z-index:2}
.menu-toggle{position:absolute;left:41px;top:34px;width:46px;height:32px}
.menu-toggle span{display:block;height:5px;background:#333;margin-bottom:8px}
.brand{position:absolute;left:130px;top:24px;width:182px;height:62px;background:#fff;display:flex;align-items:center;gap:10px;padding-left:12px;border:1px solid #eee}
.brand-dot{width:30px;height:30px;border-radius:50%;background:var(--yellow)}
.brand-name{font:700 30px "Roboto",Arial,sans-serif;color:var(--ink)}
.main-nav{position:absolute;right:58px;top:74px;display:flex;gap:34px;font-size:17px;color:var(--ink)}
.main-nav a{color:inherit;text-decoration:none;padding-bottom:4px}
.main-nav .active{border-bottom:3px solid var(--orange)}

/* hero */
.hero{position:absolute;left:0;top:100px;width:1200px;height:572px;background:linear-gradient(180deg,var(--hero-top),var(--hero-bottom))}
.hero-video{position:absolute;left:49px;top:90px;width:647px;height:384px;background:radial-gradient(circle at 50% 45%,#b9b9b9,#7a7a7a 70%);box-shadow:0 4px 14px rgba(0,0,0,.35);overflow:hidden}
.video-controls{position:absolute;left:0;bottom:0;width:100%;height:40px;background:rgba(40,40,40,.55);display:flex;align-items:center;padding:0 14px;gap:14px}
.progress{flex:1;height:4px;background:rgba(255,255,255,.5);position:relative}
.progress i{position:absolute;left:0;top:0;height:4px;width:72%;background:var(--orange)}
.hero-title{position:absolute;left:748px;top:176px;font:700 38px/46px "Roboto",Arial,sans-serif;color:#fff;letter-spacing:.5px}
.btn-join{position:absolute;left:753px;top:282px;width:222px;height:57px;border-radius:4px;background:linear-gradient(#fbb62e,var(--orange-dark));color:#fff;font:700 25px/57px "Ubuntu",Arial,sans-serif;text-align:center;box-shadow:0 2px 4px rgba(0,0,0,.3)}

/* section titles */
.section-title{position:absolute;left:0;width:1200px;text-align:center;font:300 35px "Roboto",Arial,sans-serif;color:#777}

/* packages */
.packages{position:absolute;left:84px;top:769px;display:flex;gap:20px}
.package-card{width:244px;height:317px;border:1px solid var(--line);border-radius:4px;box-shadow:0 2px 4px rgba(0,0,0,.15);overflow:hidden;background:#fff;position:relative}
.package-head{height:135px;display:flex;align-items:center;justify-content:center;position:relative}
.package-add{position:absolute;right:8px;top:8px;width:24px;height:24px;background:#c9c9c9;color:#fff;font:700 18px/24px Arial,sans-serif;text-align:center;border-radius:2px}
.package-body{padding:10px 10px 0;font-size:14px;line-height:19px;color:#444}
.package-author{margin-top:18px;font-size:15px}
.package-date{margin-top:18px;font-size:11px;color:var(--muted)}
.package-meta{position:absolute;left:0;bottom:0;width:100%;height:46px;border-top:1px solid var(--line);display:flex;align-items:center;padding:0 10px;gap:6px;font-size:12px;color:var(--muted)}
.package-price{margin-left:auto;font:700 28px "Roboto",Arial,sans-serif;color:var(--orange)}
.btn-browse{position:absolute;left:84px;top:1127px;width:1038px;height:68px;border:1px solid #b8b8b8;border-radius:4px;background:linear-gradient(#f2f2f2,#c8c8c8);text-align:center;font:400 28px/68px "Roboto",Arial,sans-serif;color:var(--link-blue)}

/* features */
.features-intro{position:absolute;left:200px;top:1320px;width:800px;text-align:center;font-size:18px;line-height:24px;color:var(--ink)}
.features{position:absolute;left:190px;top:1441px;display:grid;grid-template-columns:439px 439px;grid-auto-rows:217px}
.feature{display:flex;gap:12px}
.feature-icon{width:135px;height:135px;border-radius:50%;background:var(--yellow);flex:none;display:flex;align-items:center;justify-content:center;box-shadow:0 2px 3px rgba(0,0,0,.12)}
.feature h3{font:400 20px "Roboto",Arial,sans-serif;color:#555;margin-top:34px}
.feature h3.current{color:var(--orange)}
.feature p{font-size:12px;line-height:16px;color:#777;margin-top:14px;width:230px}

.btn-signup{position:absolute;left:488px;top:2820px;width:222px;height:57px;border-radius:4px;background:linear-gradient(#fbb62e,var(--orange-dark));color:#fff;font:700 26px/57px "Ubuntu",Arial,sans-serif;text-align:center}

/* footer */
.site-footer{position:absolute;left:0;top:2939px;width:1200px;height:312px;background:var(--footer);color:#fff}
.footer-links{position:absolute;left:81px;top:72px;list-style:none;font-size:11px;line-height:22px}
.footer-col{position:absolute;top:42px;font-size:11px;line-height:15px}
.footer-col h4{font:500 17px "Roboto",Arial,sans-serif;margin-bottom:12px;letter-spacing:.5px}
.footer-col .accent{color:var(--yellow)}
.tweet{display:flex;gap:8px;margin-bottom:14px}
.tweet b{width:13px;height:13px;border-radius:50%;background:#3aa7e0;flex:none;margin-top:2px}
.news-form{display:flex;margin-top:12px}
.news-input{width:146px;height:24px;background:#333;border:1px solid #555;font-size:10px;color:#999;padding:5px}
.news-btn{width:32px;height:24px;background:var(--orange)}
.social{display:flex;gap:6px;margin-top:8px}
.social i{width:20px;height:20px;background:#d9d9d9;border-radius:2px}
.social i.hot{background:var(--orange)}
.share-btn{display:inline-block;margin:12px 0 0 108px;background:var(--orange);font-size:10px;padding:2px 8px;border-radius:2px}
</style>
</head>
<body>

<header class="site-header">
  <div class="menu-toggle"><span></span><span></span><span></span></div>
  <div class="brand"><span class="brand-dot"></span><span class="brand-name">Brivora</span></div>
  <nav class="main-nav"><a href="#">Features</a><a href="#" class="active">Login</a></nav>
</header>

<section class="hero">
  <div class="hero-video" role="img" aria-label="Intro video: smiling learner in front of a chalkboard with doodled learning icons">
    <div class="video-controls">
      <svg width="16" height="18" viewBox="0 0 16 18"><path d="M0 0L16 9L0 18Z" fill="#fff"/></svg>
      <div class="progress"><i></i></div>
      <svg width="20" height="16" viewBox="0 0 20 16"><path d="M0 5H5L11 0V16L5 11H0Z" fill="#fff"/></svg>
      <svg width="22" height="16" viewBox="0 0 22 16"><rect x="1" y="1" width="20" height="14" fill="none" stroke="#fff" stroke-width="2"/></svg>
    </div>
  </div>
  <h1 class="hero-title">YOUR LEARNING<br>JOURNEY STARTS HERE</h1>
  <div class="btn-join">Join Now!</div>
</section>

<h2 class="section-title" style="top:698px">Discover Learning Packages</h2>

<div class="packages">
  <article class="package-card">
    <div class="package-head" style="background:var(--yellow)"><span class="package-add">+</span>
      <svg width="74" height="60" viewBox="0 0 74 60"><path d="M4 4H44V32H22L12 42V32H4Z" fill="#fff"/><path d="M30 20H70V48H62V58L52 48H30Z" fill="#fff" opacity=".9"/></svg></div>
    <div class="package-body">Cras scelerisque et ante eget lacinia iaculis ullamcorper augue.<div class="package-author">Mr John Smith</div><div class="package-date">12th August 2013</div></div>
    <div class="package-meta">◉ 102 &nbsp;★ 4.6<span class="package-price">50$</span></div>
  </article>
  <article class="package-card">
    <div class="package-head" style="background:var(--yellow-2)"><span class="package-add">+</span>
      <svg width="74" height="50" viewBox="0 0 74 50"><rect x="14" y="4" width="56" height="40" fill="#fff"/><path d="M14 4L42 26L70 4" fill="none" stroke="#f7bd2c" stroke-width="3"/><path d="M0 16H10M3 26H10M6 36H10" stroke="#fff" stroke-width="3"/></svg></div>
    <div class="package-body">Cras scelerisque et ante eget lacinia iaculis ullamcorper augue.<div class="package-author">Mr John Smith</div><div class="package-date">12th August 2013</div></div>
    <div class="package-meta">◉ 102 &nbsp;★ 4.6<span class="package-price">75$</span></div>
  </article>
  <article class="package-card">
    <div class="package-head" style="background:var(--yellow-3)"><span class="package-add">+</span>
      <svg width="56" height="64" viewBox="0 0 56 64"><path d="M20 2H36V22L54 60H2L20 22Z" fill="#fff"/><circle cx="26" cy="46" r="5" fill="#f9cb55"/><circle cx="36" cy="52" r="3" fill="#f9cb55"/></svg></div>
    <div class="package-body">Cras scelerisque et ante eget lacinia iaculis ullamcorper augue.<div class="package-author">Mr John Smith</div><div class="package-date">12th August 2013</div></div>
    <div class="package-meta">◉ 102 &nbsp;★ 3.6<span class="package-price">75$</span></div>
  </article>
  <article class="package-card">
    <div class="package-head" style="background:var(--yellow-4)"><span class="package-add">+</span>
      <svg width="60" height="56" viewBox="0 0 60 56"><rect x="4" y="28" width="9" height="24" fill="#fff"/><rect x="18" y="14" width="9" height="38" fill="#fff"/><rect x="32" y="4" width="9" height="48" fill="#fff"/><rect x="46" y="20" width="9" height="32" fill="#fff"/></svg></div>
    <div class="package-body">Cras scelerisque et ante eget lacinia iaculis ullamcorper augue.<div class="package-author">Mr John Smith</div><div class="package-date">12th August 2013</div></div>
    <div class="package-meta">◉ 102 &nbsp;★ 3.6<span class="package-price">75$</span></div>
  </article>
</div>

<div class="btn-browse">Browse Packages</div>

<h2 class="section-title" style="top:1246px">Our Features</h2>
<p class="features-intro">Neque porro quisquam est, qui dolorem ipsum quia dolor sit amet, consectetur, adipisci velit, sed quia non numquam eius modi tempora incidunt ut labore et dolore</p>

<div class="features">
  <div class="feature"><div class="feature-icon"><svg width="62" height="54" viewBox="0 0 62 54"><path d="M4 4H58V38H24L12 50V38H4Z" fill="#fff" stroke="var(--icon)" stroke-width="3"/><circle cx="20" cy="21" r="3" fill="var(--icon)"/><circle cx="31" cy="21" r="3" fill="var(--icon)"/><circle cx="42" cy="21" r="3" fill="var(--icon)"/></svg></div>
    <div><h3 class="current">Language and Linguistic</h3><p>Sed non massa qui nisi tincidunt posuere et amet vitae sem. Praesent sed convallis quam.</p></div></div>
  <div class="feature"><div class="feature-icon"><svg width="62" height="50" viewBox="0 0 62 50"><rect x="22" y="2" width="18" height="10" fill="none" stroke="var(--icon)" stroke-width="4"/><rect x="2" y="10" width="58" height="38" rx="3" fill="var(--icon)"/></svg></div>
    <div><h3>Business and Finance</h3><p>Sed non massa qui nisi tincidunt posuere et amet vitae sem. Praesent sed convallis quam.</p></div></div>
  <div class="feature"><div class="feature-icon"><svg width="60" height="54" viewBox="0 0 60 54"><path d="M4 18H16L46 2V52L16 36H4Z" fill="var(--icon)"/><rect x="12" y="36" width="10" height="16" fill="var(--icon)"/></svg></div>
    <div><h3>Marketing</h3><p>Sed non massa qui nisi tincidunt posuere et amet vitae sem. Praesent sed convallis quam.</p></div></div>
  <div class="feature"><div class="feature-icon"><svg width="62" height="54" viewBox="0 0 62 54"><rect x="2" y="2" width="58" height="38" rx="3" fill="var(--icon)"/><rect x="7" y="7" width="48" height="28" fill="#e9e4da"/><rect x="24" y="40" width="14" height="8" fill="var(--icon)"/><rect x="16" y="48" width="30" height="4" fill="var(--icon)"/></svg></div>
    <div><h3>IT and Software</h3><p>Sed non massa qui nisi tincidunt posuere et amet vitae sem. Praesent sed convallis quam.</p></div></div>
  <div class="feature"><div class="feature-icon"><svg width="60" height="52" viewBox="0 0 60 52"><path d="M14 2H46L58 16L30 50L2 16Z" fill="#e9e4da" stroke="var(--icon)" stroke-width="3"/><path d="M2 16H58M22 2L30 50L38 2" fill="none" stroke="var(--icon)" stroke-width="2"/></svg></div>
    <div><h3>Lifestyle</h3><p>Sed non massa qui nisi tincidunt posuere et amet vitae sem. Praesent sed convallis quam.</p></div></div>
  <div class="feature"><div class="feature-icon"><svg width="58" height="58" viewBox="0 0 58 58"><path d="M56 2C36 2 22 14 14 30L28 44C44 36 56 22 56 2Z" fill="var(--icon)"/><path d="M14 30L4 32L16 20M28 44L26 54L38 42" fill="var(--icon)"/><path d="M12 40L4 54L18 46" fill="var(--icon)"/></svg></div>
    <div><h3>Personal Development</h3><p>Sed non massa qui nisi tincidunt posuere et amet vitae sem. Praesent sed convallis quam.</p></div></div>
  <div class="feature"><div class="feature-icon"><svg width="62" height="48" viewBox="0 0 62 48"><rect x="2" y="10" width="58" height="36" rx="4" fill="var(--icon)"/><rect x="20" y="2" width="20" height="10" fill="var(--icon)"/><circle cx="31" cy="28" r="12" fill="#e9e4da"/></svg></div>
    <div><h3>Photography</h3><p>Sed non massa qui nisi tincidunt posuere et amet vitae sem. Praesent sed convallis quam.</p></div></div>
  <div class="feature"><div class="feature-icon"><svg width="60" height="54" viewBox="0 0 60 54"><path d="M30 52L6 28C-2 18 4 2 17 2C23 2 28 6 30 10C32 6 37 2 43 2C56 2 62 18 54 28Z" fill="#e9e4da"/></svg></div>
    <div><h3>Health and Fitnes</h3><p>Sed non massa qui nisi tincidunt posuere et amet vitae sem. Praesent sed convallis quam.</p></div></div>
  <div class="feature"><div class="feature-icon"><svg width="58" height="58" viewBox="0 0 58 58"><path d="M40 4L54 18L18 54H4V40Z" fill="var(--icon)"/><path d="M4 40L18 54H4Z" fill="#e9e4da"/></svg></div>
    <div><h3>Education and Teaching</h3><p>Sed non massa qui nisi tincidunt posuere et amet vitae sem. Praesent sed convallis quam.</p></div></div>
  <div class="feature"><div class="feature-icon"><svg width="50" height="58" viewBox="0 0 50 58"><path d="M16 8L48 2V42" fill="none" stroke="var(--icon)" stroke-width="5"/><path d="M16 8V48" stroke="var(--icon)" stroke-width="5"/><ellipse cx="10" cy="48" rx="9" ry="7" fill="var(--icon)"/><ellipse cx="42" cy="42" rx="9" ry="7" fill="var(--icon)"/></svg></div>
    <div><h3>Music</h3><p>Sed non massa qui nisi tincidunt posuere et amet vitae sem. Praesent sed convallis quam.</p></div></div>
  <div class="feature"><div class="feature-icon"><svg width="62" height="50" viewBox="0 0 62 50"><path d="M2 8L16 22L31 4L46 22L60 8V48H2Z" fill="var(--icon)"/></svg></div>
    <div><h3>Hotels and Hospitality</h3><p>Sed non massa qui nisi tincidunt posuere et amet vitae sem. Praesent sed convallis quam.</p></div></div>
  <div class="feature"><div class="feature-icon"><svg width="46" height="60" viewBox="0 0 46 60"><rect x="4" y="2" width="38" height="10" rx="2" fill="var(--icon)"/><path d="M6 14H40L36 58H10Z" fill="var(--icon)"/><rect x="8" y="26" width="30" height="12" fill="#e9e4da"/></svg></div>
    <div><h3>Food and Baverage</h3><p>Sed non massa qui nisi tincidunt posuere et amet vitae sem. Praesent sed convallis quam.</p></div></div>
</div>

<h2 class="section-title" style="top:2744px">Improve Your Skills</h2>
<div class="btn-signup">Sign Up</div>

<footer class="site-footer">
  <ul class="footer-links"><li>Home</li><li>About us</li><li>Features</li><li>Blog</li><li>Pricing</li><li>Careers</li><li>Support</li><li>Contact us</li></ul>
  <div class="footer-col" style="left:279px;width:250px">
    <h4>Brivora</h4>
    <p>Learning for Organisations and Educational Institutions Launching Soon!</p><br>
    <p>Brivora will be launching services to integrate Brivora's learning platform into Organisations and Learning Institutes to support Online, Interactive and Blended Learning. For enquiries, <span class="accent">contact hello@brivora-learn.example</span></p>
  </div>
  <div class="footer-col" style="left:612px;width:220px">
    <h4>LAST TWEETS</h4>
    <div class="tweet"><b></b><p>at dolore magnam aliquam qu aerat voluptatem. Ut enim ad minima veniam.<br>5 hours ago</p></div>
    <div class="tweet"><b></b><p>at dolore magnam aliquam qu aerat voluptatem. Ut enim ad minima veniam.<br>5 hours ago</p></div>
  </div>
  <div class="footer-col" style="left:916px;width:220px">
    <h4>NEWSLETTER</h4>
    <p>Neque porro quisquam est, qui dolore m ipsum quia dolor sit amet, consecte tur, adipisci velit.</p>
    <div class="news-form"><div class="news-input">email address</div><div class="news-btn"></div></div>
    <p style="margin-top:12px">Follow us</p>
    <div class="social"><i></i><i></i><i></i><i></i><i class="hot"></i><i></i><i></i></div>
    <span class="share-btn">Sharely</span>
  </div>
</footer>

</body>
</html>
```